Lotstallmart.com Webpage Design

Design Brief for lotstallmart.com (Copy of Brief also in attached Word file)

Name of Website- lotstallmart.com (existing logo and look & feel of website to be changed)

Logo - Finalised. The logo files are attached with the brief as “logo.jpeg”. The “Blue- Grey” version of the logo is for use on lighter backgrounds and the “Orange-White” version of the logo is for use on darker backgrounds. (A full Black version of the logo is also attached). Both versions may be used in different parts of the website. All attached files are in .png format.
Status - The website in functional and is undergoing user trials. However, we want to improve the look & feel of the website so at it seems
a. cotemporary,
b. Easy to Navigate
c. professional and
d. Vibrant.

Please visit ‘lotstallmart.com’ to check out the website and its functionalities – please use it only as a reference for the features & functions to be provided, however the designer should use a ‘Free Hand’ in designing the composition of various parts of the webpage without getting too influenced by the existing design

Objective of the Website ‘lotstallmart.com –
a. It is a portal focussed on listing of ‘Retail’ specific real-estate properties by developers, owners and realty brokers. The properties shall listed under the following four categories-
i. Retail Malls
ii. Shopping Complexes
iii. High-street shops
iv. Retail Warehouses
*refer lotstallmart.com for better clarity

b. The abovementioned properties shall be listed either for ‘Sale’ or ‘rent\lease’ or both

c. Users shall visit the site in case they wish to acquire a retail \ shop space either on ‘sale’ or ‘rent’. These Users would be able to specify the ‘Search Criteria’ through the tool-bars provided on the website – the ‘Search Criteria’ shall comprise of ‘Type of space category’, ‘City’, ‘Locality’, transaction type ie ‘Rent \ Sale’ and ‘Area Range’

d. The main revenue model for the website shall be listing fee ( or advertising charges ) payable by those listing their properties on the website.

Three Main Pages of Website (lotstallmart.com) that need to be designed -
a. Main Home Page (visit the web link - http://lotstallmart.com/ ) - The main home page has the “Search Toolbar” for specifying of Search Criteria by the User. It shall also have the following features & functions-
i. Main Advertising Banner
ii. Featured Projects
iii. New Launches
iv. Toolbar with buttons – ‘Advertise with Us’, ‘Listings Alert’, ‘Mart Wizards’, ‘Advertiser Login’

b. Property Listings Page (visit the web link - http://lotstallmart.com/gurgaon-in-india ) - The List of property options that match the Criteria specified by the ‘User’ get displayed on this page.

c. Property Detail Page - When the ‘User’ clicks on the “More….” Button on the ‘Property Listings Page’ (given in point b. above) the web page with the details of the property opens. (For Example – visit the web link - http://lotstallmart.com/vorne-Shopping-Complex-vorne-quadrion-gurgaon-636 )

Note:- Please refer to attached ‘Shopping’ related images the designer may use them on the website to provide a look & feel of retail if required – either separately or rotate in a single window

Target Market(s)

Retailers & Investors looking for retail space, Real Estate Brokers, Developers

Industry/Entity Type

Advertising

Number of Pages Required

3 page

Requirements
Must have
• Refer to existing site lotstallmart.com -- all the existing functionalities are a must have.
Nice to have
• The Designer may use the retail related images on the website if required for making it more vibrant. Refer attached images Shopping(1-6).jpg

```html
<!DOCTYPE html>
<html lang="en">
<head>
<meta charset="utf-8">
<title>Lotstallmart.com – Home</title>
<link href="https://fonts.googleapis.com/css2?family=Fira+Sans:wght@300;400;500;600&display=swap" rel="stylesheet">
<style>
  :root{
    --brand-blue:#0a97e3;
    --brand-blue-dark:#0780c4;
    --text-blue:#1a8fd6;
    --logo-grey:#5f6b73;
    --panel:rgba(120,120,115,0.62);
    --panel-line:rgba(255,255,255,0.35);
    --white:#ffffff;
    --ink:#222222;
    --field:#f4f4f4;
  }
  *{box-sizing:border-box;margin:0;padding:0}
  html,body{width:1200px;height:900px;overflow:hidden;background:var(--white);font-family:"Fira Sans",Arial,sans-serif;color:var(--ink)}
  .page{width:1200px;height:900px;position:relative;background:var(--white)}

  .city-bar{height:30px;background:var(--brand-blue);display:flex;justify-content:center;align-items:center;gap:0;color:var(--white);font-size:14px;font-weight:500}
  .city-bar span{padding:0 7px;border-right:1px solid rgba(255,255,255,.8);line-height:14px}
  .city-bar span:last-child{border-right:none}

  .site-header{height:100px;display:flex;align-items:center;justify-content:space-between;padding:0 70px 0 190px;border-bottom:2px solid var(--brand-blue)}
  .brand{display:flex;align-items:center;gap:10px}
  .brand-dot{width:30px;height:30px;border-radius:50%;background:var(--brand-blue)}
  .brand-text{display:flex;flex-direction:column}
  .brand-name{font-size:28px;font-weight:500;color:var(--logo-grey);letter-spacing:-.3px;line-height:1}
  .brand-tag{font-size:8px;font-weight:500;color:var(--logo-grey);text-transform:uppercase;letter-spacing:.6px;margin-top:4px}

  .main-nav{display:flex;align-items:center;gap:40px;font-size:16px;color:var(--text-blue)}
  .account{display:flex;flex-direction:column;align-items:flex-end;gap:8px}
  .list-property{font-size:12px;color:#1d5f9a}
  .account-links{display:flex;align-items:center;gap:18px;font-size:15px;color:var(--text-blue)}
  .login-btn{background:var(--brand-blue);color:var(--white);border-radius:14px;padding:4px 12px;font-size:14px}

  .hero{position:relative;height:560px}
  .hero-photo{position:absolute;inset:0;background:linear-gradient(100deg,#d8cfc2 0%,#bfb4a6 30%,#e08a3a 55%,#c9bfb1 70%,#e6e2da 100%)}

  .search-panel{position:absolute;left:215px;top:60px;width:340px;height:470px;background:var(--panel);padding:46px 34px 0;color:var(--white)}
  .screw{position:absolute;width:14px;height:14px;border-radius:50%;background:#d9d9d9;border:2px solid #9a9a9a}
  .screw.tl{left:10px;top:10px}.screw.tr{right:10px;top:10px}.screw.bl{left:10px;bottom:10px}.screw.br{right:10px;bottom:10px}
  .panel-title{font-size:21px;font-weight:500;margin-bottom:22px}
  .formats{display:grid;grid-template-columns:1fr 1fr;gap:10px 8px;font-size:13px;margin-bottom:26px}
  .formats label{display:flex;align-items:center;gap:5px}
  .radio{width:11px;height:11px;border-radius:50%;background:#e0e0e0;border:1px solid #999}
  .field-row{display:flex;align-items:center;justify-content:space-between;margin-bottom:22px;font-size:14px}
  .select{width:140px;height:40px;background:var(--field);border:1px solid #bbb;color:#666;font-size:12px;display:flex;align-items:center;justify-content:space-between;padding:0 10px 0 26px}
  .select svg{width:10px;height:6px}
  .search-btn{margin-left:164px;margin-top:8px;display:inline-flex;align-items:center;gap:8px;background:var(--brand-blue);color:var(--white);font-size:14px;font-weight:600;padding:10px 14px;text-transform:uppercase}
  .search-btn svg{width:18px;height:18px}

  .featured{text-align:center;padding-top:40px;display:flex;justify-content:center;align-items:baseline;gap:16px}
  .featured h2{font-size:34px;font-weight:400;color:var(--text-blue)}
  .featured small{font-size:18px;color:var(--ink)}
</style>
</head>
<body>
<div class="page">
  <nav class="city-bar" aria-label="Cities">
    <span>Bangalore</span><span>Chennai</span><span>Greater Nodia</span><span>Gurgaon</span><span>Hyderabad</span><span>Jaipur</span><span>Khanna</span><span>Kolkatta</span><span>Mumbai</span><span>Nodia</span><span>Pune</span><span>Surat</span>
  </nav>

  <header class="site-header">
    <div class="brand">
      <div class="brand-dot"></div>
      <div class="brand-text">
        <span class="brand-name">lotstallmart</span>
        <span class="brand-tag">India's leading portal for retail space</span>
      </div>
    </div>
    <nav class="main-nav">
      <a>Advertise with us</a>
      <a>Listing Alert</a>
      <a>Mart Wizards</a>
      <div class="account">
        <span class="list-property">List Your Property Here</span>
        <div class="account-links"><a>Signup</a><span class="login-btn">Login</span></div>
      </div>
    </nav>
  </header>

  <section class="hero">
    <div class="hero-photo" role="img" aria-label="Shopping mall interior with a happy shopper carrying colourful shopping bags"></div>
    <form class="search-panel">
      <span class="screw tl"></span><span class="screw tr"></span><span class="screw bl"></span><span class="screw br"></span>
      <div class="panel-title">Select Retail Format</div>
      <div class="formats">
        <label><span class="radio"></span>Retail Malls</label>
        <label><span class="radio"></span>Shopping Complex</label>
        <label><span class="radio"></span>High Street Shops</label>
        <label><span class="radio"></span>Retail Warehouses</label>
      </div>
      <div class="field-row"><span>Sell Or Rent Or Both</span><div class="select">--Select--<svg viewBox="0 0 10 6"><path d="M0 0h10L5 6z" fill="#555"/></svg></div></div>
      <div class="field-row"><span>Select City</span><div class="select">--Select--<svg viewBox="0 0 10 6"><path d="M0 0h10L5 6z" fill="#555"/></svg></div></div>
      <div class="field-row"><span>Select Locality</span><div class="select">--Select--<svg viewBox="0 0 10 6"><path d="M0 0h10L5 6z" fill="#555"/></svg></div></div>
      <div class="field-row"><span>Enter Keywords</span><div class="select">--Select--<svg viewBox="0 0 10 6"><path d="M0 0h10L5 6z" fill="#555"/></svg></div></div>
      <span class="search-btn">Search Now
        <svg viewBox="0 0 18 18"><circle cx="7" cy="7" r="5" fill="none" stroke="#fff" stroke-width="2.2"/><path d="M11 11l5 5" stroke="#fff" stroke-width="2.6" stroke-linecap="round"/></svg>
      </span>
    </form>
  </section>

  <section class="featured">
    <h2>Featured Retail Projects</h2>
    <small>Across India</small>
  </section>
</div>
</body>
</html>
```